Commit To Be The Best! - Marketing, Training, Managment for Multifamily Professionals

Flyer for training event. I have to be able to edit location, times, speakers, cost,
We will have 2 to 4 speakers for each event. Each event may have a different topic relating to the main topic (Marketing, Training, Management). The idea is to get as many people to open or pick up the fly and say "I have to attend" this seminar. We are the experts in the industry and want to portray this with the flyer. Each speaker will have a topic and a certain amount of time. Each topic will be different.
Updates

Project Deadline Extended
Reason: I apologize for the new design deadline. I've been traveling extensively for work and unable to view submissions. Currently I am not traveling and able to dedicate time to view all of the wonderful submissions. I'm looking forward to selecting one. Thank you all for your understanding.

Target Market(s)

Multifamily - Apartment Communities, Owners, Apartment Associations, Leasing Agents, Marketing Directors, Managers, Presidents,

Industry/Entity Type

Marketing

Colors

Designer to choose colors to be used in the design.

Requirements
Must have
• Editable flyer. I have to be able to edit; location, times/date, speaker, cost, description.
• Sponsored by KTV Power attached Logo for KTV
Nice to have
• Spot for photo of each speaker (2-4) speaker

```html
<!DOCTYPE html>
<html lang="en">
<head>
<meta charset="utf-8">
<title>Training Event Flyer</title>
<link rel="stylesheet" href="https://fonts.googleapis.com/css2?family=Bebas+Neue&family=Roboto:wght@400;700&display=swap">
<style>
  :root {
    --blue-deep: #1d4f86;
    --blue-steel: #3f6792;
    --blue-mid: #2d5e95;
    --white: #ffffff;
    --ink: #1f1f1f;
    --photo-a: #c9c2bd;
    --photo-b: #8f8a8e;
    --portrait-a: #e6e8ec;
    --portrait-b: #a7adb6;
  }
  * { margin: 0; padding: 0; box-sizing: border-box; }
  html, body { width: 797px; height: 1200px; overflow: hidden; background: var(--white); }
  .flyer { position: relative; width: 797px; height: 1200px; background: var(--white); overflow: hidden; font-family: "Roboto", Arial, sans-serif; }
  .flyer-shapes { position: absolute; inset: 0; }
  .event-heading {
    position: absolute; left: 44px; top: 44px;
    font-family: "Bebas Neue", "Arial Narrow", sans-serif;
    font-size: 108px; line-height: 1; letter-spacing: 1px;
    color: var(--blue-steel); white-space: nowrap;
  }
  .event-title {
    position: absolute; left: 26px; top: 527px;
    font-family: "Bebas Neue", "Arial Narrow", sans-serif;
    font-size: 118px; line-height: 1; color: var(--white); white-space: nowrap;
  }
  .speakers {
    position: absolute; left: 40px; top: 680px; width: 720px;
    display: grid; grid-template-columns: repeat(3, 1fr); column-gap: 24px;
  }
  .speaker { text-align: center; }
  .speaker-photo {
    width: 136px; height: 136px; margin: 0 auto 10px;
    border-radius: 50%; border: 4px solid var(--blue-deep);
    background: radial-gradient(circle at 50% 40%, var(--portrait-a), var(--portrait-b));
  }
  .speaker-name { font-size: 22px; font-weight: 700; color: var(--blue-mid); margin-bottom: 10px; }
  .speaker-bio { font-size: 14px; line-height: 1.3; color: var(--ink); text-align: justify; }
  .sponsor {
    position: absolute; right: 46px; top: 1092px;
    display: flex; align-items: center; gap: 10px;
    font-size: 15px; font-weight: 700; color: var(--ink);
  }
  .sponsor-name { font-size: 28px; font-weight: 700; color: var(--ink); }
</style>
</head>
<body>
<main class="flyer">
  <svg class="flyer-shapes" width="797" height="1200" viewBox="0 0 797 1200">
    <defs>
      <linearGradient id="eventPhotoTone" x1="0" y1="0" x2="1" y2="1">
        <stop offset="0" stop-color="var(--photo-a)"/>
        <stop offset="1" stop-color="var(--photo-b)"/>
      </linearGradient>
    </defs>
    <polygon class="corner-band" points="620,0 797,0 797,400" fill="var(--blue-mid)"/>
    <polygon class="corner-stripe" points="655,0 680,0 797,250 797,300" fill="var(--white)"/>
    <polygon class="heading-rule" points="0,178 520,160 525,170 0,188" fill="var(--blue-deep)"/>
    <polygon class="seminar-photo" role="img" aria-label="Photo of a seminar room with attendees seated at tables and microphones"
      points="0,198 520,182 700,470 690,500 0,560" fill="url(#eventPhotoTone)"/>
    <polyline class="frame-line" points="520,168 740,520" stroke="var(--blue-deep)" stroke-width="10" fill="none"/>
    <polyline class="frame-line" points="548,168 770,510" stroke="var(--blue-deep)" stroke-width="6" fill="none"/>
    <polygon class="title-band" points="0,555 430,510 495,620 0,660" fill="var(--blue-deep)"/>
    <polygon points="510,565 545,560 560,590 525,594" fill="var(--blue-deep)"/>
    <polygon points="560,558 575,556 590,586 575,588" fill="var(--blue-deep)"/>
    <polygon points="585,555 598,553 613,583 600,585" fill="var(--blue-deep)"/>
    <polygon points="608,552 620,550 635,580 623,582" fill="var(--blue-deep)"/>
    <polygon class="footer-band" points="340,1200 797,1200 797,1140 620,1150" fill="var(--blue-deep)"/>
  </svg>

  <h1 class="event-heading">Training Event</h1>
  <h2 class="event-title">Title Here</h2>

  <section class="speakers">
    <article class="speaker">
      <div class="speaker-photo" role="img" aria-label="Speaker portrait"></div>
      <h3 class="speaker-name">Lorem Ipsum</h3>
      <p class="speaker-bio">Lorem Ipsum is simply dummy text of the printing and typesetting industry. Lorem Ipsum has been the industry's standard dummy text ever since the 1500s, when an unknown printer took a galley of type and scrambled it to make a type specimen book. It has survived not only five centuries, but also the leap into electronic typesetting, remaining essentially unchanged.</p>
    </article>
    <article class="speaker">
      <div class="speaker-photo" role="img" aria-label="Speaker portrait"></div>
      <h3 class="speaker-name">Lorem Ipsum</h3>
      <p class="speaker-bio">Lorem Ipsum is simply dummy text of the printing and typesetting industry. Lorem Ipsum has been the industry's standard dummy text ever since the 1500s, when an unknown printer took a galley of type and scrambled it to make a type specimen book. It has survived not only five centuries, but also the leap into electronic typesetting, remaining essentially unchanged.</p>
    </article>
    <article class="speaker">
      <div class="speaker-photo" role="img" aria-label="Speaker portrait"></div>
      <h3 class="speaker-name">Lorem Ipsum</h3>
      <p class="speaker-bio">Lorem Ipsum is simply dummy text of the printing and typesetting industry. Lorem Ipsum has been the industry's standard dummy text ever since the 1500s, when an unknown printer took a galley of type and scrambled it to make a type specimen book. It has survived not only five centuries, but also the leap into electronic typesetting, remaining essentially unchanged.</p>
    </article>
  </section>

  <footer class="sponsor">
    <span class="sponsor-label">Sponsored by</span>
    <span class="sponsor-name">KTV</span>
  </footer>
</main>
</body>
</html>
```